Sophisticated, clean website reflecting my feminine, playful side to sell my abstract art,

I need a website no more than 3 pages to showcase my paintings, a little about me and some contact info. I do abstracts so looking for something a little edgy, yet feminine and current.
Updates

Hi there, These are some artists websites that I Iike: Marnelvoss.com (I like how airy it is) peterwallombry.com garethpolvens.com (I like how it scrolls) I'll need a place for a photo ( a headshot-i do not have it yet so I'll need to be able to upload that later) as well as an area for my bio. Also, it's important that I will be able to upload any new photos and descriptions easily so it should be user friendly. Lastly, I like in a sunny place so would like to have this seem upbeat and playful as that is how i like to paint. thanks-I'm trying to upload my photos now -

Target Market(s)

ppl ages 35-70 who want large scale art for their homes

Industry/Entity Type

art

Coding

Coded - Design and coding required

Number of Pages Required

3 page

Colors

Designer to choose colors to be used in the design.

Requirements
Must have
• photos of my art, a place for my bio, be easy to reach me. tasteful-nothing too "in your face" -my clients are pretty high end and organized. They like clean lines
Nice to have
• sophisticated background, muted tones in the back-similar clean font throughout-no cursive
Should not have
• too many dark areas. Too many blocks of color. Too serious.

```html
<!DOCTYPE html>
<html lang="en">
<head>
<meta charset="utf-8">
<title>Lena Vardell — Abstract Paintings</title>
<link rel="stylesheet" href="https://fonts.googleapis.com/css2?family=Barlow+Condensed:wght@600;700&family=Barlow:wght@300;600&family=Big+Shoulders+Display:wght@900&family=Nunito+Sans:wght@300;400&display=swap">
<style>
  :root {
    --ink: #111111;
    --paper: #ffffff;
    --gold: #b58a4f;
    --gold-soft: #c9a574;
    --wood-light: #f1e8d8;
    --wood-mid: #e6d8bf;
    --frame-wood: #e4a266;
    --frame-edge: #c98447;
    --cream-line: #e8ddcf;
    --footer-bg: #000000;
    --footer-rule: #4a4a4a;
    --body-text: #3a3a3a;
  }
  * { box-sizing: border-box; margin: 0; padding: 0; }
  html, body { width: 1200px; height: 2558px; overflow: hidden; background: var(--paper); }
  body { position: relative; font-family: "Nunito Sans", sans-serif; color: var(--ink); }

  /* Header */
  .site-header { position: absolute; top: 0; left: 0; width: 1200px; height: 100px; background: var(--paper); }
  .brand { position: absolute; display: flex; align-items: center; gap: 14px;
    font-family: "Barlow Condensed", sans-serif; font-weight: 700; font-size: 40px; letter-spacing: .5px; text-transform: uppercase; white-space: nowrap; }
  .brand-square { width: 54px; height: 54px; background: var(--ink); display: block; }
  .site-header .brand { left: 87px; top: 22px; }
  .main-nav { position: absolute; top: 34px; left: 553px; display: flex; gap: 68px;
    font-family: "Barlow Condensed", sans-serif; font-weight: 700; font-size: 22px; text-transform: uppercase; }
  .main-nav .active { position: relative; }
  .main-nav .active::after { content: ""; position: absolute; left: 24px; right: 24px; bottom: -8px; height: 2px; background: var(--ink); }
  .social-dot { position: absolute; width: 34px; height: 34px; border-radius: 50%; background: var(--ink); }
  .site-header .social-dot { left: 1029px; top: 31px; }

  /* Hero */
  .hero { position: absolute; top: 100px; left: 0; width: 1200px; height: 636px;
    background: linear-gradient(180deg, var(--wood-light) 0%, #efe4d1 45%, var(--wood-mid) 100%); }
  .hero-greeting { position: absolute; left: 114px; top: 190px; font-family: "Barlow", sans-serif; font-weight: 300; font-size: 28px; letter-spacing: 1px; }
  .hero-title { position: absolute; left: 110px; top: 225px; font-family: "Big Shoulders Display", sans-serif; font-weight: 900;
    font-size: 84px; line-height: 76px; letter-spacing: 2px; text-transform: uppercase; }
  .hero-arrow { position: absolute; top: 289px; }
  .hero-arrow.prev { left: 36px; }
  .hero-arrow.next { left: 1138px; }
  .hero-frame { position: absolute; left: 485px; top: 59px; width: 614px; height: 512px;
    background: var(--frame-wood); border: 2px solid var(--frame-edge); padding: 18px; }
  .hero-painting { width: 100%; height: 100%; background: linear-gradient(160deg, #cfc8cc 0%, #a98086 100%); }

  /* About */
  .about { position: absolute; top: 736px; left: 0; width: 1200px; height: 614px; background: var(--paper); }
  .portrait-frame { position: absolute; left: 122px; top: 125px; width: 374px; height: 390px; border: 2px solid var(--cream-line); padding: 12px; }
  .portrait-frame::before { content: ""; position: absolute; left: -4px; top: -5px; width: 78px; height: 72px; border-left: 5px solid var(--cream-line); border-top: 5px solid var(--cream-line); }
  .portrait-frame::after { content: ""; position: absolute; right: -5px; bottom: -6px; width: 78px; height: 72px; border-right: 5px solid var(--cream-line); border-bottom: 5px solid var(--cream-line); }
  .portrait { width: 100%; height: 100%; background: linear-gradient(180deg, #eef1f3 0%, #c9ced6 60%, #9aa3b0 100%); }
  .section-heading { font-family: "Barlow Condensed", sans-serif; font-weight: 700; font-size: 50px; line-height: 1; text-transform: uppercase; }
  .heading-rule { width: 73px; height: 3px; background: var(--gold-soft); }
  .about .section-heading { position: absolute; left: 566px; top: 125px; }
  .about .heading-rule { position: absolute; left: 568px; top: 180px; }
  .about-copy { position: absolute; left: 570px; top: 196px; width: 520px; font-size: 17px; line-height: 27.5px; font-weight: 300; color: var(--body-text); text-align: justify; }
  .about-copy p + p { margin-top: 14px; }
  .outline-button { position: absolute; display: flex; align-items: center; justify-content: center; border: 2px solid var(--ink);
    font-family: "Barlow", sans-serif; font-weight: 600; font-size: 18px; color: var(--gold); text-transform: uppercase; letter-spacing: .5px; }
  .about .outline-button { left: 570px; top: 429px; width: 181px; height: 50px; }

  /* Gallery */
  .gallery { position: absolute; top: 1350px; left: 0; width: 1200px; height: 1001px;
    background: linear-gradient(115deg, #ece6dd 0%, #f7f3ee 30%, #f8f4ef 60%, #f3e4d6 85%, #f0d3c8 100%); }
  .gallery .section-heading { position: absolute; left: 0; width: 1200px; top: 78px; text-align: center; font-size: 52px; }
  .gallery .heading-rule { position: absolute; left: 568px; top: 136px; }
  .painting-grid { position: absolute; left: 94px; top: 187px; display: grid; grid-template-columns: repeat(3, 318px); grid-auto-rows: 287px; column-gap: 29px; row-gap: 27px; }
  .painting { display: block; }
  .painting.rust { background: linear-gradient(180deg, #ddd6d3 0%, #c08a78 100%); }
  .painting.violet { background: linear-gradient(180deg, #d8d2d6 0%, #a793b5 100%); }
  .painting.bloom { background: linear-gradient(180deg, #d6cfd2 0%, #a07a7c 100%); }
  .painting.meadow { background: linear-gradient(180deg, #b8d2a8 0%, #5d9c63 100%); }
  .painting.swirl { background: linear-gradient(180deg, #e8e1d2 0%, #b7b49e 100%); }
  .painting.stripes { background: linear-gradient(180deg, #5f9e98 0%, #3b6070 100%); }
  .gallery .outline-button { left: 497px; top: 837px; width: 208px; height: 56px; font-size: 20px; }

  /* Footer */
  .site-footer { position: absolute; top: 2351px; left: 0; width: 1200px; height: 207px; background: var(--footer-bg); color: var(--paper); }
  .site-footer .brand { left: 91px; top: 40px; font-size: 36px; gap: 10px; }
  .site-footer .brand-square { width: 45px; height: 45px; background: var(--paper); }
  .footer-nav { position: absolute; top: 56px; left: 436px; display: flex; gap: 59px;
    font-family: "Barlow Condensed", sans-serif; font-weight: 700; font-size: 22px; text-transform: uppercase; }
  .site-footer .social-dot { left: 991px; top: 50px; width: 34px; height: 34px; background: var(--paper); }
  .footer-rule { position: absolute; left: 75px; top: 128px; width: 1052px; height: 2px; background: var(--footer-rule); }
  .copyright { position: absolute; left: 0; width: 1160px; top: 154px; text-align: center; font-family: "Barlow Condensed", sans-serif; font-size: 13px; letter-spacing: .3px; text-transform: uppercase; }
</style>
</head>
<body>

<header class="site-header">
  <div class="brand"><span class="brand-square"></span>Lena Vardell</div>
  <nav class="main-nav">
    <span class="active">About Me</span>
    <span>Gallery</span>
    <span>Contact</span>
  </nav>
  <span class="social-dot"></span>
</header>

<section class="hero">
  <svg class="hero-arrow prev" width="30" height="48" viewBox="0 0 30 48" aria-hidden="true">
    <polyline points="24,4 6,24 24,44" fill="none" stroke="#3a3a3a" stroke-width="6"/>
  </svg>
  <p class="hero-greeting">WELCOME TO</p>
  <h1 class="hero-title">Lena<br>Vardell</h1>
  <div class="hero-frame">
    <div class="hero-painting" role="img" aria-label="Featured abstract painting in plum and rose tones"></div>
  </div>
  <svg class="hero-arrow next" width="30" height="48" viewBox="0 0 30 48" aria-hidden="true">
    <polyline points="6,4 24,24 6,44" fill="none" stroke="#3a3a3a" stroke-width="6"/>
  </svg>
</section>

<section class="about">
  <div class="portrait-frame">
    <div class="portrait" role="img" aria-label="Portrait photograph of the artist"></div>
  </div>
  <h2 class="section-heading">About Me</h2>
  <div class="heading-rule"></div>
  <div class="about-copy">
    <p>Lorem ipsum dolor sit amet, consectetur adipiscing elit, sed do eiusmod tempor incididunt ut labore et dolore magna aliqua. Ut enim ad minim veniam, quis nostrud exercitation ullamco laboris</p>
    <p>Duis aute irure dolor in reprehenderit in voluptate velit esse cillum dolore eu fugiat nulla pariatur. Excepteur sint occaecat cupidatat non proident, sunt in culpa qui officia deserunt mollit anim id est laborum.Sed ut perspiciatis unde omnis iste natus</p>
  </div>
  <a class="outline-button">Learn More</a>
</section>

<section class="gallery">
  <h2 class="section-heading">Painting Gallery</h2>
  <div class="heading-rule"></div>
  <div class="painting-grid">
    <div class="painting rust" role="img" aria-label="Abstract painting in rust tones"></div>
    <div class="painting violet" role="img" aria-label="Abstract painting in violet tones"></div>
    <div class="painting bloom" role="img" aria-label="Abstract painting in plum and rose tones"></div>
    <div class="painting meadow" role="img" aria-label="Abstract painting in green tones"></div>
    <div class="painting swirl" role="img" aria-label="Abstract painting in ochre and blue tones"></div>
    <div class="painting stripes" role="img" aria-label="Abstract painting in teal and navy tones"></div>
  </div>
  <a class="outline-button">View More</a>
</section>

<footer class="site-footer">
  <div class="brand"><span class="brand-square"></span>Lena Vardell</div>
  <nav class="footer-nav">
    <span>Home</span>
    <span>About Me</span>
    <span>Gallery</span>
    <span>Contact</span>
  </nav>
  <span class="social-dot"></span>
  <div class="footer-rule"></div>
  <p class="copyright">© 2022 Lena Vardell | All Rights Reserved</p>
</footer>

</body>
</html>
```